Web Developer Wordpress theme

I'm a web developer but a poor designer so i need somebody to design me a cool and professional WordPress theme. I specialize in shopping cart developments and modifications as well as hosting for these system so would like the design to show this off. I am UK based and want this to also come across in the design.
As for colors and layout i am open mined just use your imaginantion i will let know what i think of your designs.
also forgot to mention my business name is valtrique
and my exsiting site is valtrique.co.uk

```html
<!DOCTYPE html>
<html lang="en">
<head>
<meta charset="utf-8">
<title>Valtrique – Serious Web Development</title>
<link href="https://fonts.googleapis.com/css2?family=Ubuntu:wght@400;500&family=Open+Sans:wght@400;600&display=swap" rel="stylesheet">
<style>
:root{
  --topbar:#191919;
  --hero:#262626;
  --hero-light:#333333;
  --page:#f0f0f0;
  --white:#ffffff;
  --ink:#222222;
  --body:#3a3a3a;
  --muted:#c9c9c9;
  --orange:#ef8c1b;
  --orange-dark:#d97606;
  --blue:#3a7ab4;
  --amber:#e8900f;
  --cyan:#29a3cc;
  --footer:#242424;
  --footer-bottom:#1b1b1b;
  --footer-text:#bdbdbd;
  --rule:#d8d8d8;
}
*{margin:0;padding:0;box-sizing:border-box}
html,body{width:890px;height:1200px;overflow:hidden}
body{position:relative;background:var(--page);font-family:"Open Sans",Arial,sans-serif;color:var(--body)}
.abs{position:absolute}
a{color:inherit}

.topbar{left:0;top:0;width:890px;height:20px;background:var(--topbar)}
.account{right:72px;top:4px;font-size:10px;color:#9a9a9a;font-family:"Ubuntu",sans-serif}
.account span{margin:0 6px}

.hero{left:0;top:20px;width:890px;height:368px;background:linear-gradient(180deg,#2c2c2c,#222 60%,#262626)}
.brand{left:43px;top:50px;display:flex;align-items:center;gap:8px}
.brand-dot{width:18px;height:18px;border-radius:50%;background:var(--orange)}
.brand-name{font-family:"Ubuntu",sans-serif;font-size:36px;font-weight:400;color:var(--orange);line-height:1}
.brand-tag{left:100px;top:93px;font-size:7px;letter-spacing:2px;color:#7a7a7a}

.nav{left:321px;top:20px;height:80px;display:flex;font-family:"Ubuntu",sans-serif;font-size:12px;color:#e6e6e6}
.nav a{text-decoration:none;padding:24px 13px 0;border-left:1px solid #3a3a3a;height:80px}
.nav a.active{background:var(--hero-light);border-left:none;padding:24px 15px 0}

.hero-title{left:92px;top:148px;font-family:"Ubuntu",sans-serif;font-size:27px;color:var(--white);font-weight:400}
.hero-copy{left:92px;top:183px;width:370px;font-size:10.5px;line-height:14.5px;color:var(--muted)}
.hero-copy p+p{margin-top:8px}
.hero-button{left:92px;top:292px;width:167px;height:24px;border-radius:4px;background:linear-gradient(var(--orange),var(--orange-dark));color:var(--white);font-family:"Ubuntu",sans-serif;font-size:12px;line-height:24px;text-align:center}
.hero-visual{left:473px;top:115px;width:330px;height:245px;border-radius:8px;background:linear-gradient(160deg,#dcdcdc,#9da3a8 55%,#5b6066)}
.slider-dots{left:413px;top:354px;display:flex;gap:5px}
.slider-dots i{width:9px;height:9px;border-radius:50%;background:#e8e8e8}

.addon{top:378px;width:262px;height:140px;border:3px solid var(--white);box-shadow:0 6px 8px rgba(0,0,0,.15);color:var(--white)}
.addon h3{position:absolute;left:10px;top:10px;font-family:"Ubuntu",sans-serif;font-size:17px;font-weight:400}
.addon .price{position:absolute;left:12px;top:42px;width:53px;height:50px;background:var(--white);color:#111;font-family:"Ubuntu",sans-serif;font-size:15px;line-height:18px;padding:8px 0 0 5px}
.addon .price small{font-size:11px;display:block}
.addon p{position:absolute;left:71px;top:40px;width:180px;font-size:9.6px;line-height:13px}
.addon .notch{position:absolute;right:22px;top:-3px;width:0;height:0;border-left:11px solid transparent;border-right:11px solid transparent;border-top:12px solid var(--white)}
.addon-blue{left:29px;background:var(--blue)}
.addon-amber{left:301px;background:var(--amber)}
.addon-cyan{left:578px;top:375px;background:var(--cyan)}

.section-title{font-family:"Ubuntu",sans-serif;font-size:17px;color:var(--ink);font-weight:400}
.section-rule{height:1px;background:linear-gradient(90deg,#c8c8c8,transparent)}
.welcome-copy{left:35px;top:588px;width:510px;font-size:10.5px;line-height:14.5px;color:var(--body)}
.divider{left:585px;top:535px;width:1px;height:375px;background:#dadada}

.service{background:var(--white);width:264px;height:82px}
.service .icon{position:absolute;left:8px;top:14px}
.service h4{position:absolute;left:43px;top:11px;font-size:11px;font-weight:400;text-decoration:underline;color:#333}
.service p{position:absolute;left:43px;top:26px;width:210px;font-size:10.3px;line-height:14px;color:#333}

.quote-title{left:609px;top:552px}
.quote{left:614px;width:230px;font-size:10.5px;line-height:14.5px;color:#333}
.quote-mark{font-family:Georgia,serif;font-size:26px;color:#888;line-height:1}
.quote-by{background:var(--white);font-size:11.5px;font-style:italic;color:#333;padding:2px 6px;border-radius:3px}
.view-more{left:612px;top:867px;font-family:"Ubuntu",sans-serif;font-size:13px;color:#8a8a8a}

.footer{left:0;top:928px;width:890px;height:224px;background:var(--footer)}
.footer-notch{top:928px;width:0;height:0;border-left:8px solid transparent;border-right:8px solid transparent;border-top:10px solid var(--page)}
.footer h5{font-family:"Ubuntu",sans-serif;font-size:16px;font-weight:400;color:#e3e3e3}
.page-links{left:41px;top:972px;width:170px;list-style:none;font-size:10px;color:var(--footer-text)}
.page-links li{padding:3px 4px 5px;border-bottom:1px solid #333;height:21.3px}
.page-links li:last-child{border-bottom:none}
.recent{left:275px;top:978px;width:205px;font-size:10px;line-height:12.6px;color:var(--footer-text)}
.recent a{font-weight:600;text-decoration:underline;color:#ddd}
.recent p{margin-top:10px}
.social-icons{left:546px;top:976px;display:flex;gap:5px}
.social-icons i{width:25px;height:25px;border-radius:50%;background:#2f6aa8;border:2px solid #dcdcdc}
.social-links{left:550px;top:1014px;font-size:10px;line-height:17.5px;color:var(--footer-text)}
.social-links a{display:block}

.footer-bottom{left:0;top:1152px;width:890px;height:48px;background:var(--footer-bottom);font-size:10px;font-weight:600;color:#d0d0d0}
.copyright{left:34px;top:12px}
.legal{right:32px;top:12px}
</style>
</head>
<body>

<div class="abs topbar"></div>
<div class="abs account">LOG IN<span>|</span>REGISTER</div>

<header class="abs hero"></header>
<div class="abs brand"><i class="brand-dot"></i><span class="brand-name">valtrique</span></div>
<div class="abs brand-tag">serious web development</div>

<nav class="abs nav">
  <a class="active">HOME</a><a>SERVICES</a><a>ADDONS</a><a>OUR E-COMMERCE HOSTING</a><a>BLOG</a><a>CONTACT US</a>
</nav>

<svg class="abs" style="left:30px;top:163px" width="24" height="84" viewBox="0 0 24 84"><polyline points="20,2 3,42 20,82" fill="none" stroke="#9a9a9a" stroke-width="1.5"/></svg>
<svg class="abs" style="left:838px;top:163px" width="24" height="84" viewBox="0 0 24 84"><polyline points="4,2 21,42 4,82" fill="none" stroke="#9a9a9a" stroke-width="1.5"/></svg>

<h1 class="abs hero-title">Uk Freelance Web Developer</h1>
<div class="abs hero-copy">
  <p>Brightmoor Web Studio is a professional website design company dedicated to provide excellent services. We at Brightmoor Web Studio think graphic design as a combination and collaboration of ideas and technology.</p>
  <p>Our Website Design team give an unforgettable impression on the customers and the clients. We can assure you that this is the best place for requirement of yours regarding website design solutions</p>
</div>
<div class="abs hero-button">LEARN MORE ABOUT US</div>
<div class="abs hero-visual" role="img" aria-label="Laptop showing a website design on its screen"></div>
<div class="abs slider-dots"><i></i><i></i><i></i></div>

<div class="abs addon addon-blue"><span class="notch"></span><h3>Corvale Addons</h3><div class="price">$400<small>*form</small></div><p>When considering advanced web development project, finding the right answers to the hard questions is a challenge for any firm, it includes expertise and enables Brightmoor to specialize</p></div>
<div class="abs addon addon-amber"><span class="notch"></span><h3>Corvale Addons</h3><div class="price">$400<small>*form</small></div><p>When considering advanced web development project, finding the right answers to the hard questions is a challenge for any firm, it includes expertise and enables Brightmoor to specialize</p></div>
<div class="abs addon addon-cyan"><span class="notch"></span><h3>Corvale Addons</h3><div class="price">$400<small>*form</small></div><p>When considering advanced web development project, finding the right answers to the hard questions is a challenge for any firm, it includes expertise and enables Brightmoor to specialize</p></div>

<h2 class="abs section-title" style="left:35px;top:549px">Welcome To Valtrique Web Devlopment</h2>
<div class="abs section-rule" style="left:35px;top:576px;width:520px"></div>
<div class="abs welcome-copy">E-Commerce is a major progress in technology that has changed the way in which the customers now purchase information, products and the services. It’s the new way of providing an opportunity to make your products and services available in the global market 24 hours a day through Internet<br>Brightmoor Web Studio is specialized in handling advanced web projects and the ongoing projects that require permanent maintenance and support.</div>

<h2 class="abs section-title" style="left:35px;top:693px">Services Overview</h2>
<div class="abs section-rule" style="left:35px;top:717px;width:520px"></div>

<div class="abs service" style="left:32px;top:728px">
  <svg class="icon" width="26" height="28" viewBox="0 0 26 28"><ellipse cx="11" cy="6" rx="9" ry="3.5" fill="#b9c6d6"/><rect x="2" y="6" width="18" height="16" fill="#9fb1c6"/><ellipse cx="11" cy="22" rx="9" ry="3.5" fill="#8aa0b8"/><line x1="2" y1="12" x2="20" y2="12" stroke="#e8eef4"/><line x1="2" y1="17" x2="20" y2="17" stroke="#e8eef4"/></svg>
  <h4>First Services here</h4><p>Static website are the which are usually been used and are benefited through the Professionals and Small Companies.</p>
</div>
<div class="abs service" style="left:304px;top:728px;width:256px">
  <svg class="icon" style="left:17px;top:16px" width="28" height="28" viewBox="0 0 28 28"><circle cx="14" cy="14" r="13" fill="#f2b233"/><path d="M14 14 L14 1 A13 13 0 0 1 27 14Z" fill="#e14c4c"/><path d="M14 14 L27 14 A13 13 0 0 1 14 27Z" fill="#3aa0de"/><path d="M14 14 L14 27 A13 13 0 0 1 1 14Z" fill="#6fc24a"/><circle cx="14" cy="14" r="5" fill="#fff"/></svg>
  <h4 style="left:56px">First Services here</h4><p style="left:56px;width:196px">Static website are the which are usually been used and are benefited through the Professionals and Small Companies.</p>
</div>
<div class="abs service" style="left:32px;top:818px">
  <svg class="icon" width="26" height="28" viewBox="0 0 26 28"><ellipse cx="11" cy="6" rx="9" ry="3.5" fill="#b9c6d6"/><rect x="2" y="6" width="18" height="16" fill="#9fb1c6"/><ellipse cx="11" cy="22" rx="9" ry="3.5" fill="#8aa0b8"/><line x1="2" y1="12" x2="20" y2="12" stroke="#e8eef4"/><line x1="2" y1="17" x2="20" y2="17" stroke="#e8eef4"/></svg>
  <h4>First Services here</h4><p>Static website are the which are usually been used and are benefited through the Professionals and Small Companies.</p>
</div>
<div class="abs service" style="left:304px;top:818px;width:256px">
  <svg class="icon" style="left:14px;top:14px" width="30" height="28" viewBox="0 0 30 28"><polyline points="2,3 7,3 11,19 25,19" fill="none" stroke="#666" stroke-width="2"/><path d="M8 7 H28 L25 16 H10Z" fill="#9a9a9a"/><circle cx="12" cy="24" r="2.5" fill="#555"/><circle cx="23" cy="24" r="2.5" fill="#555"/></svg>
  <h4 style="left:54px">First Services here</h4><p style="left:54px;width:198px">Static website are the which are usually been used and are benefited through the Professionals and Small Companies.</p>
</div>

<div class="abs divider"></div>
<h2 class="abs section-title quote-title">What Our Customer Say</h2>
<svg class="abs" style="left:792px;top:546px" width="34" height="24" viewBox="0 0 34 24"><ellipse cx="17" cy="10" rx="16" ry="9" fill="#c4c4c4"/><path d="M8 16 L5 23 L14 18Z" fill="#c4c4c4"/></svg>

<div class="abs quote" style="top:584px"><span class="abs quote-mark" style="left:-10px;top:-2px">“</span>Brightmoor Web Studio is a professional website design company dedicated to provide excellent services.</div>
<div class="abs quote-by" style="left:609px;top:644px;width:166px">by Harriet Pennick.com</div>
<div class="abs quote" style="top:695px"><span class="abs quote-mark" style="left:-12px;top:-6px">“</span>E-Commerce is a major progress in technology that has changed the way in which the customers now purchase information, products and the services.<br>It’s the new way of providing an opportunity to make your products and services available in the global market 24 hours a day through Internet</div>
<div class="abs quote-by" style="left:607px;top:825px;width:165px">by Harriet Pennick.com</div>
<div class="abs view-more">VIEW MORE</div>

<footer class="abs footer"></footer>
<div class="abs footer-notch" style="left:41px"></div>
<div class="abs footer-notch" style="left:275px"></div>
<div class="abs footer-notch" style="left:546px"></div>

<h5 class="abs" style="left:41px;top:945px">Page Links</h5>
<ul class="abs page-links"><li>Main</li><li>Services</li><li>Addons</li><li>E-Commerce Hosting</li><li>Recent Blog</li><li>Contact Us</li></ul>

<h5 class="abs" style="left:275px;top:948px">Recent Posts</h5>
<div class="abs recent"><a>Tittle of blog here</a><p>Static website are the which are usually been used and are benefited through the Professionals and Small Companies. The companies with fewer budgets can promote their products and services through the static website and gain a lot.</p><p style="margin-top:8px"><a style="font-weight:400;color:var(--footer-text)">view all</a></p></div>

<h5 class="abs" style="left:539px;top:945px">Connect with Us</h5>
<div class="abs social-icons"><i></i><i style="background:#2d7bb6"></i><i style="background:#3aa7dc"></i></div>
<div class="abs social-links"><a>Friendhub</a><a>Workline</a><a>Chirper</a></div>

<div class="abs footer-bottom">
  <span class="abs copyright">copyright © 2011 company name &nbsp; All right reserved</span>
  <span class="abs legal">Terms &amp; Condition &nbsp;|&nbsp; Privacy Policy</span>
</div>

</body>
</html>
```